Business Card Design for Flood Rescue 360 - Property Restoration Professionals

I need a business card designed for Flood Rescue 360. We are a full-service property restoration solution. Providing water, fire, smoke & storm restoration as well as mold remediation and full remodel or reconstruction to homes and businesses across Dallas-Fort Worth, TX.
Target Market(s)
home and business owners with insurance covered property damage from water, fire or storm related damage
Industry/Entity Type
property restoration
Contact Information for Business Card
Marcus Pelley General Manager Cell: 214-555-0193 Office: 469-555-0148 email: Marcus@FloodRescue360.example services: Water, Fire, Mold, Reconstruction Tagline: Urgency for Your Water Emergency!
Look and feel
Each slider illustrates characteristics of the customer's brand and the style your logo design should communicate.

```html
<!DOCTYPE html>
<html lang="en">
<head>
<meta charset="utf-8">
<title>Flood Rescue 360 – Business Card</title>
<link rel="stylesheet" href="https://fonts.googleapis.com/css2?family=Montserrat:wght@400;500;700;800&display=swap">
<style>
  :root {
    --stage: #1d1d1d;
    --card-white: #f6f6f6;
    --card-dark: #1f1f1f;
    --brand-blue: #17acdf;
    --brand-grey: #6d6d6d;
    --ink: #222222;
    --divider: #8a8a8a;
    --light-text: #f2f2f2;
  }
  * { margin: 0; padding: 0; box-sizing: border-box; }
  html, body {
    width: 1200px; height: 1059px; overflow: hidden;
    background: var(--stage);
    font-family: "Montserrat", sans-serif;
  }
  .canvas { position: relative; width: 1200px; height: 1059px; }

  .card {
    position: absolute;
    border-radius: 16px;
    overflow: hidden;
  }
  .card-front {
    left: 257px; top: 89px; width: 687px; height: 390px;
    background: var(--card-white);
  }
  .card-back {
    left: 254px; top: 546px; width: 693px; height: 394px;
    background: var(--card-dark);
  }

  .brand-name {
    position: absolute; left: 26px; top: 150px;
    color: var(--brand-blue);
    font-weight: 800; font-size: 35px; line-height: 40px;
    letter-spacing: -0.5px;
    text-transform: uppercase;
  }

  .divider {
    position: absolute; left: 300px; top: 110px;
    width: 1px; height: 171px; background: var(--divider);
  }

  .person { position: absolute; left: 325px; top: 108px; }
  .person-name {
    color: var(--brand-blue); font-weight: 700; font-size: 27px;
    letter-spacing: 0.5px; line-height: 30px; text-transform: uppercase;
  }
  .person-title {
    color: var(--ink); font-weight: 400; font-size: 17px; line-height: 22px;
    letter-spacing: 0.3px;
  }

  .contact-list { position: absolute; left: 323px; top: 177px; list-style: none; }
  .contact-item {
    display: flex; align-items: center; height: 29px;
    color: var(--ink); font-size: 16px; font-weight: 400; letter-spacing: 0.2px;
    white-space: nowrap;
  }
  .contact-icon { width: 12px; height: 12px; margin-right: 9px; flex: none; }

  .swoosh { position: absolute; left: 0; bottom: 0; }

  .back-pattern {
    position: absolute; inset: 0;
    background: linear-gradient(100deg, #1c1c1c 0%, #262626 45%, #4a4a4a 80%, #6a6a6a 100%);
  }
  .back-text {
    position: absolute; left: 0; width: 693px; top: 294px;
    text-align: center; color: var(--light-text);
    font-size: 18px; font-weight: 400; letter-spacing: 0.6px; line-height: 29px;
  }
  .services .dot { color: var(--brand-blue); margin: 0 6px; }
</style>
</head>
<body>
<main class="canvas">

  <section class="card card-front" aria-label="Card front">
    <div class="brand-name">Flood<br>Rescue 360</div>
    <div class="divider"></div>

    <div class="person">
      <h1 class="person-name">Marcus Pelley</h1>
      <p class="person-title">General Manager</p>
    </div>

    <ul class="contact-list">
      <li class="contact-item">
        <svg class="contact-icon" viewBox="0 0 12 12" aria-hidden="true"><path fill="#17acdf" d="M1 4c0-2 2-3 5-3s5 1 5 3l-2 1-1-1.5H4L3 5zM2 6l2-2h4l2 2v4H2z"/></svg>
        469-555-0148
      </li>
      <li class="contact-item">
        <svg class="contact-icon" viewBox="0 0 12 12" aria-hidden="true"><rect x="3" y="0.5" width="6" height="11" rx="1.2" fill="none" stroke="#17acdf" stroke-width="1.4"/><circle cx="6" cy="9.5" r="0.7" fill="#17acdf"/></svg>
        214-555-0193
      </li>
      <li class="contact-item">
        <svg class="contact-icon" viewBox="0 0 12 12" aria-hidden="true"><path fill="#17acdf" d="M0 5l6-4 6 4v6H0z"/><path fill="none" stroke="#fff" stroke-width="0.9" d="M0.5 5.5L6 9l5.5-3.5"/></svg>
        Marcus@FloodRescue360.example
      </li>
      <li class="contact-item">
        <svg class="contact-icon" viewBox="0 0 12 12" aria-hidden="true"><circle cx="6" cy="6" r="5.5" fill="#17acdf"/><path fill="#fff" d="M3 3.5c1 0 2 .5 2 1.5s-1 1-1 2 1 1.5 1 2.5c-1.5-.5-2.5-2-2.5-3.5zM7 2.5c1 .5 2 1.5 2 3-1 0-1.5-.5-2-1.5z"/></svg>
        www.FloodRescue360.example
      </li>
    </ul>

    <svg class="swoosh" width="687" height="50" viewBox="0 0 687 50" aria-hidden="true">
      <path fill="#6d6d6d" d="M120 50 C300 20 500 8 632 8 L560 12 C420 20 300 35 230 50 Z"/>
      <path fill="#17acdf" d="M230 50 C360 28 520 12 687 11 L687 50 Z"/>
    </svg>
  </section>

  <section class="card card-back" aria-label="Card back">
    <div class="back-pattern" role="img" aria-label="Repeating pattern of the brand symbol, fading from dark to silver across the card"></div>
    <div class="back-text">
      <p class="services">Water<span class="dot">•</span>Fire<span class="dot">•</span>Mold<span class="dot">•</span>Reconstruction</p>
      <p class="tagline">Urgency for Your Water Emergency!</p>
    </div>
  </section>

</main>
</body>
</html>
```